Create Website for new company called "Verdale Lodge 37"

Verdale Lodge 37 is a new business situated in Southwestern Colorado. We are creating a business that will rent out spaces where clients can grow their own marijuana. Picture a large green house with partitioned spaces that are secured by a lock. Best way to envision this would be to think of a storage business that rents out storage rooms. The difference is that we will be having the units inside a green house ( for growing purposes) Picture a small area that is secured by locks, Picture an area that has the ability to provide state of the art security, cameras etc. We want to focus our efforts on professionals, blue collar workers and end users of marijuana. Our emphasis is in the area of assisting those whom wish to grow their own plants. We want to provide them a safe facility in which to do that. . Keep in mind that we also build custom grow rooms at clients homes and provide a grow pod (lease these) where a small grow unit will be delivered and picked up from our clients whom want to lease a unit for a short amount of time. We have a business card ( just designed) and will send that information to those whom express an interests in this project. We want to be able to sign people up for our services by entering an agreement and signing the agreement while on the internet. We want to provide our services to those whom consume recreational and medical marijuana. This site will need to gather information I.e email addresses so that we can followup with offers. This is a tremendous opportunity for the right designer. We will be creating many more websites as other states come on line and make marijuana legal to consume. Use the business card model for a point of reference of how we envision the concept. That is a business card we just recently printed. The hands and the plant is our logo so far. Open to suggestions. There will be three levels of service. Bronze, Silver, Gold or Platinum. We will also have a retail biz down the road but not at the present time.

Target Market(s)

Ages 21-60

Industry/Entity Type

Medical

Logo Text

Verdale Lodge 37.

Number of Pages Required

5+ page

Requirements
Must have
• Clean appearance not to busy , easily navigable from link to link, page to page. Must have ability down the road to enter into a contractual agreement via the website. Must use our provided logo and example of that is on our business card that will be uploaded here shortly. We would like to have the colors that are on the business card however if you have suggestions or color schemes that you want us to consider that is okay.
Nice to have
• Nice to have a animation of seed to weed and how clients can save a tremendous amount of money growing their own cannabis. Nice to have testimonial page or feedback page. Have a membership component to website,
Should not have
• No flashing lights, etc. Not to busy in terms of animations.

```html
<!DOCTYPE html>
<html lang="en">
<head>
<meta charset="utf-8">
<title>Verdale Lodge 37</title>
<link href="https://fonts.googleapis.com/css2?family=Bebas+Neue&family=Nunito+Sans:wght@400;600&display=swap" rel="stylesheet">
<style>
:root{
  --forest:#3c5a48;
  --page:#e8e8e8;
  --white:#ffffff;
  --orange:#d27f3a;
  --green:#1e8a3a;
  --heading:#2f4a3c;
  --text:#555555;
  --panel:#303c38;
  --leaf-dark:#2f5a22;
  --leaf-light:#8cbf4a;
}
*{margin:0;padding:0;box-sizing:border-box}
html,body{width:913px;height:1200px;overflow:hidden}
body{position:relative;background:var(--page);font-family:"Nunito Sans",sans-serif;color:var(--text)}
.band-top{position:absolute;left:0;top:0;width:913px;height:96px;background:var(--forest)}
.band-bottom{position:absolute;left:0;top:1066px;width:913px;height:134px;background:var(--forest)}
.sheet{position:absolute;left:140px;top:26px;width:633px;height:1090px;background:var(--white)}
.header{position:absolute;left:140px;top:26px;width:633px;height:70px;background:linear-gradient(#fbfbfb,#ececec)}
.brand{position:absolute;left:148px;top:58px;font-family:"Bebas Neue",sans-serif;font-size:30px;line-height:30px;color:#3a3f3c;letter-spacing:.3px}
.tagline{position:absolute;left:342px;top:52px;font-size:11.5px;color:#555}
.nav{position:absolute;left:140px;top:96px;width:633px;height:44px;background:linear-gradient(90deg,var(--orange) 0%,var(--orange) 45%,#9b7a3a 70%,#4d6b2c 100%);display:flex;align-items:center;padding-left:23px;gap:0}
.nav a{font-family:"Bebas Neue",sans-serif;color:#fff;font-size:16.5px;text-decoration:none;margin-right:26px;letter-spacing:.2px}
.hero{position:absolute;left:140px;top:140px;width:633px;height:314px;background:radial-gradient(circle at 20% 40%,#c9d6b0 0%,#7c9a55 30%,transparent 60%),linear-gradient(120deg,#b9c8a4 0%,#6c8e3e 40%,#3f6e22 70%,#5e8f2f 100%)}
.video{position:absolute;left:182px;top:212px;width:279px;height:168px;border:3px solid #f2f2f2;background:linear-gradient(#a7967b 0%,#6f8a4a 35%,#3e6d2a 70%,#5a5a50 100%)}
.video svg{position:absolute;left:118px;top:66px}
.hero-card{position:absolute;left:461px;top:212px;width:264px;height:168px;background:rgba(30,45,25,.72);padding:24px 16px 0 17px}
.hero-card h2{font-family:"Bebas Neue",sans-serif;font-weight:400;color:var(--green);font-size:24px;line-height:24px;margin-bottom:13px}
.hero-card p{color:#eee;font-size:10px;line-height:14.4px}
.dots{position:absolute;left:436px;top:426px;display:flex;gap:4px}
.dots span{width:7px;height:7px;border:1.3px solid #fff;border-radius:50%}
.dots span:first-child{background:radial-gradient(#fff 35%,transparent 40%)}
.h-section{position:absolute;font-family:"Bebas Neue",sans-serif;font-weight:400;color:var(--heading);font-size:24px;line-height:24px}
.photo{position:absolute;border:3px solid #fff;outline:1px solid #c8c8c8;box-shadow:0 1px 2px rgba(0,0,0,.25)}
.welcome-photo{left:151px;top:522px;width:295px;height:161px;background:linear-gradient(135deg,#2e7a1e,#5aa63a 40%,#2a6618 70%,#4f9a2c)}
.welcome-text{position:absolute;left:456px;top:523px;width:310px;font-size:10px;line-height:15.6px}
.welcome-text p+p{margin-top:15.6px}
.news-item{position:absolute;left:150px;width:340px}
.news-photo{left:151px;width:136px;height:95px}
.news-body{position:absolute;left:301px;width:192px}
.news-date{font-size:7.5px;font-weight:600;color:var(--orange);line-height:10px}
.news-title{color:var(--green);font-size:11.5px;line-height:16px;margin-top:5px}
.news-text{font-size:10px;line-height:15.6px;margin-top:6px}
.testimonials{position:absolute;left:519px;top:711px;width:244px;height:383px;background:var(--panel);padding:22px 8px 0 16px}
.testimonials h2{font-family:"Bebas Neue",sans-serif;font-weight:400;color:#fff;font-size:24px;line-height:24px}
.quote{position:relative;margin-top:20px}
.quote+.quote{margin-top:15px}
.quote-mark{font-family:Georgia,serif;font-size:34px;line-height:20px;color:var(--green);font-weight:bold;height:18px}
.quote-time{position:absolute;right:0;top:2px;font-size:8px;color:var(--orange)}
.quote p{color:#eee;font-size:10px;line-height:15.6px;margin-top:8px;padding-right:4px}
.quote-author{font-size:9px;color:var(--green);margin-top:9px}
.footer-nav{position:absolute;left:140px;top:1138px;display:flex;align-items:center;font-family:"Bebas Neue",sans-serif;color:#fff;font-size:12px}
.footer-nav span.sep{margin:0 12px}
.copyright{position:absolute;left:140px;top:1161px;font-family:"Bebas Neue",sans-serif;color:#fff;font-size:12px}
.social{position:absolute;left:691px;top:1149px;display:flex;gap:7px}
.social span{width:12px;height:12px;border-radius:50%;background:#fff}
</style>
</head>
<body>
<div class="band-top"></div>
<div class="band-bottom"></div>
<div class="sheet"></div>

<header class="header"></header>
<div class="brand">Verdale Lodge 37</div>
<div class="tagline">Supporting the care &amp; cultivation of cannabis</div>

<nav class="nav">
  <a href="#">Home</a><a href="#">About Us</a><a href="#">Clients</a><a href="#">Spaces</a><a href="#">Videos</a><a href="#">FAQ'S</a><a href="#">Testimonials</a><a href="#">Contact Us</a>
</nav>

<section class="hero" role="img" aria-label="Close-up of cannabis leaves in soft daylight"></section>
<div class="video" role="img" aria-label="Video still of plants growing inside a wooden greenhouse">
  <svg width="36" height="36" viewBox="0 0 36 36"><circle cx="18" cy="18" r="16.5" fill="#333" fill-opacity=".85" stroke="#ddd" stroke-width="2"/><path d="M14 11 L26 18 L14 25 Z" fill="#fff"/></svg>
</div>
<div class="hero-card">
  <h2>Verdale Lodge</h2>
  <p>Lorem ipsum dolor sit amet, consectetur adipiscing elit, sed do eiusmod tempor incididunt ut labore et dolore magna aliqua. Ut enim ad minim veniam, quis nostrud exercitation ullamco laboris nisi ut aliquip ex ea commodo consequat.</p>
</div>
<div class="dots"><span></span><span></span><span></span><span></span></div>

<h1 class="h-section" style="left:150px;top:482px">Welcome to Verdale Lodge 37</h1>
<div class="photo welcome-photo" role="img" aria-label="Dense field of young cannabis plants"></div>
<div class="welcome-text">
  <p>Lorem ipsum dolor sit amet, consectetur adipiscing elit, sed do eiusmod tempor incididunt ut labore et dolore magna aliqua. Ut enim ad minim veniam, quis nostrud exercitation ullamco laboris nisi ut aliquip ex ea commodo consequat. Duis aute irure dolor in reprehenderit in voluptate velit esse cillum dolore eu fugiat nulla pariatur. Excepteur sint occaecat cupidatat non proident, sunt in culpa qui officia deserunt mollit anim id est laborum.</p>
  <p>Lorem ipsum dolor sit amet, consectetur adipiscing elit, sed do eiusmod tempor incididunt ut labore et dolore magna aliqua.</p>
</div>

<h2 class="h-section" style="left:150px;top:732px">Latest News</h2>

<div class="photo news-photo" style="top:779px;background:linear-gradient(135deg,#c9d3b8,#6f9c44 40%,#3f7a25 75%,#8a9a70)" role="img" aria-label="Cannabis plant leaves close-up"></div>
<article class="news-body" style="top:779px">
  <div class="news-date">DECEMBER 25TH ,2014</div>
  <div class="news-title">Lorem ipsum dolor sit amet, consectetur adipiscing elit</div>
  <div class="news-text">Et dolore magna aliqua. Ut enim ad minim veniam, quis nostrud exercitation ullamco laboris nisi ut aliquip ex ea commodo consequat. or sit amet, consectetur adipiscing elit, sed</div>
</article>

<div class="photo news-photo" style="top:943px;background:linear-gradient(160deg,#a98a60 0%,#6e9a3c 35%,#4f8a2a 70%,#8a7a5a)" role="img" aria-label="Cannabis plants inside a greenhouse"></div>
<article class="news-body" style="top:943px">
  <div class="news-date">DECEMBER 25TH ,2014</div>
  <div class="news-title">Lorem ipsum dolor sit amet, consectetur adipiscing elit</div>
  <div class="news-text">Et dolore magna aliqua. Ut enim ad minim veniam, quis nostrud exercitation ullamco laboris nisi ut aliquip ex ea commodo consequat. or sit amet, consectetur adipiscing elit, sed</div>
</article>

<aside class="testimonials">
  <h2>Clients Testimonials</h2>
  <div class="quote">
    <div class="quote-mark">&ldquo;</div>
    <div class="quote-time">2h 3mints</div>
    <p>Lorem ipsum dolor sit amet, consectetur adipiscing elit, sed do eiusmod tempor incididunt ut labore et dolore magna aliqua. Ut enim ad minim veniam, quis nostrud exercitation ullamco laboris nisi ut aliquip ex ea commodo consequat.</p>
    <div class="quote-author">- Dana Holloway -</div>
  </div>
  <div class="quote">
    <div class="quote-mark">&ldquo;</div>
    <div class="quote-time">2h 3mints</div>
    <p>Duis aute irure dolor in reprehenderit in voluptate velit esse cillum dolore eu fugiat nulla pariatur. Excepteur sint occaecat cupidatat non proident, sunt in culpa qui officia deserunt mollit anim id est laborum.</p>
    <div class="quote-author">- Dana Holloway -</div>
  </div>
</aside>

<footer>
  <div class="footer-nav">
    <span>Home</span><span class="sep">|</span><span>About Us</span><span class="sep">|</span><span>Clients</span><span class="sep">|</span><span>Spaces</span><span class="sep">|</span><span>Videos</span><span class="sep">|</span><span>FAQ'S</span><span class="sep">|</span><span>Testimonials</span><span class="sep">|</span><span>Contact Us</span>
  </div>
  <div class="copyright">&copy; 2014 Company Name ,All Rights Reserved</div>
  <div class="social" aria-label="Social links"><span></span><span></span><span></span><span></span></div>
</footer>
</body>
</html>
```